UK Online Auction Site needs a clever design

We need a contemporary landing page and registration page design for a UK auction website, that look equally at home on PC's and tablets . The design should be fresh, bright, clean, professional, robust, and familiar. We would like to see something clever but functional.

Online

```html
<!DOCTYPE html>
<html lang="en">
<head>
<meta charset="utf-8">
<title>Bidwell – UK Online Auctions</title>
<link rel="stylesheet" href="https://fonts.googleapis.com/css2?family=Arimo:wght@400;700&display=swap">
<style>
  :root {
    --brand: #0a7cc4;
    --brand-dark: #0567a8;
    --brand-light: #14a3e0;
    --ink: #555a5f;
    --ink-dark: #333;
    --muted: #8a8f94;
    --line: #d8dadc;
    --band: #f2f2f2;
    --white: #fff;
    --slate: #5b6470;
    --slate-dark: #454c56;
  }
  * { box-sizing: border-box; margin: 0; padding: 0; }
  html, body { width: 1200px; height: 675px; overflow: hidden; background: var(--white); }
  body { font-family: "Arimo", Arial, sans-serif; color: var(--ink); }
  .page { position: relative; width: 1200px; height: 675px; }

  /* Header */
  .site-header { position: absolute; left: 0; top: 0; width: 1200px; height: 88px; border-bottom: 1px solid #e3e3e3; box-shadow: 0 2px 3px rgba(0,0,0,.05); }
  .brand { position: absolute; left: 172px; top: 24px; display: flex; align-items: center; gap: 10px; color: var(--brand); font-size: 36px; font-weight: 700; letter-spacing: -0.5px; }
  .brand-dot { width: 16px; height: 16px; border-radius: 50%; background: var(--brand); }
  .main-nav { position: absolute; left: 403px; top: 0; display: flex; height: 88px; }
  .nav-item { height: 88px; border-right: 1px solid #e6e6e6; padding: 29px 0 0 0; }
  .nav-item .nav-title { display: block; color: var(--brand); font-size: 12.5px; font-weight: 700; }
  .nav-item .nav-sub { display: flex; align-items: center; gap: 6px; margin-top: 6px; color: var(--ink); font-size: 10.5px; }
  .caret { width: 0; height: 0; border-left: 4px solid transparent; border-right: 4px solid transparent; border-top: 5px solid #777; }
  .nav-sell { width: 173px; padding-left: 40px; background: linear-gradient(#0aa6e0, var(--brand-dark)); border-right: none; }
  .nav-sell .nav-title, .nav-sell .nav-sub { color: var(--white); }
  .nav-sell .caret { border-top-color: var(--white); }
  .nav-signin { width: 144px; padding-left: 31px; }
  .nav-basket { width: 146px; padding-left: 38px; }
  .nav-help { width: 163px; padding-left: 31px; }

  /* Search */
  .search-bar { position: absolute; left: 180px; top: 117px; width: 849px; height: 38px; }
  .search-label { position: absolute; left: 0; top: 13px; color: var(--brand); font-size: 12px; font-weight: 700; }
  .search-field { position: absolute; left: 106px; top: 0; width: 450px; height: 38px; border: 1px solid #c5c8cb; border-radius: 3px; background: var(--white); }
  .search-field span { position: absolute; left: 15px; top: 13px; font-size: 10px; color: var(--muted); }
  .search-options { position: absolute; right: 0; top: 8px; width: 55px; height: 22px; border-left: 1px solid #ddd; display: flex; align-items: center; justify-content: center; gap: 5px; }
  .search-button { position: absolute; left: 562px; top: 0; width: 42px; height: 38px; border-radius: 3px; background: linear-gradient(var(--slate), var(--slate-dark)); display: flex; align-items: center; justify-content: center; }
  .category-button { position: absolute; left: 642px; top: 0; width: 207px; height: 38px; border-radius: 3px; background: linear-gradient(#0a8fd2, var(--brand-dark)); color: var(--white); font-size: 13px; font-weight: 700; display: flex; align-items: center; justify-content: center; gap: 8px; }
  .category-button .caret { border-top-color: var(--white); }

  /* Welcome */
  .welcome { position: absolute; left: 172px; top: 188px; width: 857px; height: 60px; border-top: 1px solid #e2e2e2; background: linear-gradient(#efefef, var(--white)); text-align: center; padding-top: 37px; }
  .welcome h1 { color: var(--brand); font-size: 14px; font-weight: 700; }
  .welcome p { margin-top: 12px; font-size: 13px; color: var(--ink); }

  /* Features */
  .features { position: absolute; left: 172px; top: 307px; width: 857px; display: flex; justify-content: space-between; }
  .feature { width: 267px; height: 253px; border: 1px solid var(--line); border-radius: 3px; background: linear-gradient(#f7f7f7, var(--white) 30%); text-align: center; }
  .feature-art { width: 130px; height: 120px; margin: 22px auto 0; border-radius: 12px; }
  .art-safe { background: linear-gradient(160deg, #7fd05a, #3fa338 55%, #2a7f2a); }
  .art-sellers { background: linear-gradient(135deg, #dbe6f5, #b9c6d6 60%, #e8ecef); }
  .art-feedback { background: linear-gradient(135deg, #c99a6c, #7ab0e0 55%, #3f9b45); }
  .feature h2 { margin-top: 18px; color: var(--brand); font-size: 14px; font-weight: 700; }
  .feature p { margin-top: 8px; font-size: 11.5px; line-height: 20px; color: var(--ink-dark); }

  /* Footer */
  .site-footer { position: absolute; left: 172px; top: 590px; width: 857px; height: 50px; border-top: 1px solid #e2e2e2; background: linear-gradient(#efefef, var(--white)); }
  .copyright { position: absolute; left: 27px; top: 28px; font-size: 9.5px; color: var(--ink-dark); }
  .follow { position: absolute; right: 18px; top: 21px; display: flex; align-items: center; gap: 3px; font-size: 9.5px; color: var(--ink-dark); }
  .follow span { margin-right: 7px; }
  .social { width: 25px; height: 25px; }
  .social-a { background: #3b5998; }
  .social-b { background: #29a3dc; }
  .social-c { background: #dd4b39; }
</style>
</head>
<body>
<div class="page">
  <header class="site-header">
    <div class="brand"><span class="brand-dot"></span>Bidwell</div>
    <nav class="main-nav">
      <div class="nav-item nav-sell"><span class="nav-title">SELL</span><span class="nav-sub">YOUR PRODUCTS <i class="caret"></i></span></div>
      <div class="nav-item nav-signin"><span class="nav-title">SIGN-IN</span><span class="nav-sub">HELLO GUEST <i class="caret"></i></span></div>
      <div class="nav-item nav-basket"><span class="nav-title">BASKET</span><span class="nav-sub">YOUR CART <i class="caret"></i></span></div>
      <div class="nav-item nav-help"><span class="nav-title">HELP&amp; CONTACT</span><span class="nav-sub">YOUR CART <i class="caret"></i></span></div>
    </nav>
  </header>

  <div class="search-bar">
    <div class="search-label">QUICK SEARCH</div>
    <div class="search-field">
      <span>ENTER YOUR KEYWORD :</span>
      <div class="search-options">
        <svg width="13" height="13" viewBox="0 0 14 14"><circle cx="7" cy="7" r="4.5" fill="none" stroke="#999" stroke-width="3" stroke-dasharray="2 1.5"/><circle cx="7" cy="7" r="2" fill="#999"/></svg>
        <i class="caret"></i>
      </div>
    </div>
    <div class="search-button">
      <svg width="20" height="20" viewBox="0 0 20 20"><circle cx="8" cy="8" r="5.5" fill="none" stroke="#fff" stroke-width="2.4"/><line x1="12" y1="12" x2="17.5" y2="17.5" stroke="#fff" stroke-width="3" stroke-linecap="round"/></svg>
    </div>
    <div class="category-button">SHOP BY CATEGORY <i class="caret"></i></div>
  </div>

  <section class="welcome">
    <h1>WELCOME TO BIDWELL</h1>
    <p>Even if you're new or already experienced, we have everything you need to enjoy shopping on bidwell.co.uk.</p>
  </section>

  <section class="features">
    <article class="feature">
      <div class="feature-art art-safe" role="img" aria-label="Green security shield with a tick"></div>
      <h2>COMPLETELY SAFE</h2>
      <p>Bid on or buy items you're watching or<br>searching for</p>
    </article>
    <article class="feature">
      <div class="feature-art art-sellers" role="img" aria-label="Calendar with a wall clock"></div>
      <h2>PREMIUM SELLERS</h2>
      <p>Great service and the best delivery<br>when you buy from premium sellers.</p>
    </article>
    <article class="feature">
      <div class="feature-art art-feedback" role="img" aria-label="User figure with microphone and documents"></div>
      <h2>FEEDBACK RATING SYSTEM</h2>
      <p>View seller history and feedback of<br>users before you bid or buy.</p>
    </article>
  </section>

  <footer class="site-footer">
    <div class="copyright">Copyrights © 2014. Bidwell. All Rights Reserved.</div>
    <div class="follow"><span>Follow Us :</span><i class="social social-a"></i><i class="social social-b"></i><i class="social social-c"></i></div>
  </footer>
</div>
</body>
</html>
```